MRT Property - Business Cards

Looking for a business card & general letterhead, signage etc design for our new logo.

Colours:
000a20
0056a2
00b5ef
0088ce
68cef2

Fonts:
Poppins
Karla

Please keep look and feel of new brand - example in the zip package I sent.

```html
<!DOCTYPE html>
<html lang="en">
<head>
<meta charset="utf-8">
<title>MRT Property – Business Cards</title>
<link rel="stylesheet" href="https://fonts.googleapis.com/css2?family=Karla:wght@400;500&family=Poppins:wght@300;400;700&display=swap">
<style>
  :root {
    --navy: #000a20;
    --deep-blue: #0056a2;
    --bright-cyan: #00b5ef;
    --mid-blue: #0088ce;
    --light-cyan: #68cef2;
    --paper: #ffffff;
    --backdrop: #26272c;
    --ink-soft: #1c2a44;
  }
  * { box-sizing: border-box; margin: 0; padding: 0; }
  html, body { width: 1200px; height: 900px; overflow: hidden; }
  body {
    background: var(--backdrop);
    display: flex;
    flex-direction: column;
    align-items: center;
    justify-content: center;
    gap: 40px;
    font-family: "Karla", sans-serif;
  }
  .card {
    width: 700px;
    height: 400px;
    border-radius: 22px;
    position: relative;
    overflow: hidden;
  }

  /* Back of card */
  .card-back { background: var(--navy); }
  .card-back .pattern-area {
    position: absolute; inset: 0;
    background: linear-gradient(120deg, #2c4a9a 0%, #131a3a 40%, var(--navy) 100%);
  }
  .card-back .brand-name {
    position: absolute;
    right: 60px;
    top: 60px;
    font-family: "Poppins", sans-serif;
    font-weight: 700;
    font-size: 34px;
    color: var(--paper);
    letter-spacing: 1px;
  }

  /* Front of card */
  .card-front { background: var(--paper); }
  .card-front .brand-art {
    position: absolute;
    right: 0; top: 0;
    width: 330px; height: 100%;
    background: linear-gradient(160deg, var(--bright-cyan) 0%, var(--mid-blue) 45%, var(--light-cyan) 100%);
    clip-path: polygon(22% 0, 100% 0, 100% 70%, 30% 100%, 0 60%);
  }
  .card-front .details {
    position: absolute;
    left: 48px;
    top: 48px;
  }
  .brand-name-front {
    font-family: "Poppins", sans-serif;
    font-weight: 700;
    font-size: 46px;
    line-height: 1;
    color: var(--deep-blue);
    letter-spacing: 1px;
  }
  .person-name {
    margin-top: 30px;
    font-family: "Poppins", sans-serif;
    font-weight: 300;
    font-size: 26px;
    color: var(--deep-blue);
  }
  .person-title {
    font-size: 15px;
    font-weight: 500;
    color: var(--ink-soft);
    margin-top: 2px;
  }
  .address {
    margin-top: 16px;
    font-size: 14px;
    line-height: 1.35;
    color: var(--ink-soft);
  }
  .contact-list {
    list-style: none;
    margin-top: 16px;
    font-size: 14px;
    color: var(--ink-soft);
  }
  .contact-list li {
    display: flex;
    align-items: center;
    gap: 10px;
    line-height: 1.6;
  }
  .contact-list svg { width: 13px; height: 13px; flex: none; }
</style>
</head>
<body>

  <section class="card card-back" aria-label="Business card back">
    <div class="pattern-area" role="img" aria-label="Repeating brand pattern on navy, fading from blue at left to dark at right"></div>
    <div class="brand-name">MRT Property</div>
  </section>

  <section class="card card-front" aria-label="Business card front">
    <div class="brand-art" role="img" aria-label="Large brand graphic in cyan and blue tones"></div>
    <div class="details">
      <div class="brand-name-front">MRT Property</div>
      <div class="person-name">Daniel Reed</div>
      <div class="person-title">Managing Director</div>
      <div class="address">24 Harbor Oak Drive<br>Fairview, MS 39200</div>
      <ul class="contact-list">
        <li>
          <svg viewBox="0 0 16 16" aria-hidden="true"><path fill="var(--mid-blue)" d="M3.6 1.5l2.3 2.4-1.3 1.6c.9 2 2.4 3.5 4.4 4.4l1.6-1.3 2.4 2.3-1.5 2.1C6.6 12.8 3.2 9.4 1.5 4.5z"/></svg>
          555.301.4420
        </li>
        <li>
          <svg viewBox="0 0 16 16" aria-hidden="true"><rect x="1" y="3" width="14" height="10" rx="1" fill="var(--deep-blue)"/><path d="M1.5 3.8L8 9l6.5-5.2" stroke="#fff" stroke-width="1.2" fill="none"/></svg>
          info@mrtproperty.com
        </li>
        <li>
          <svg viewBox="0 0 16 16" aria-hidden="true"><circle cx="8" cy="8" r="7" fill="var(--mid-blue)"/><path d="M1 8h14M8 1c-3 3.5-3 10.5 0 14M8 1c3 3.5 3 10.5 0 14" stroke="#fff" stroke-width="1" fill="none"/></svg>
          www.mrtproperty.com
        </li>
      </ul>
    </div>
  </section>

</body>
</html>
```